Music Quizz Application

Hello,

I want a new design for my Blind test (music quizz) application on Korvex. You will find attached the images I want to replace. I need something with the same element (menu / song title) but with a different look!

Same, new icon, you have carte blanche to this one.

I am looking for something fresh…. I'm looking for something with a real artistic choice, contrast, colours, etc.

As a marketing screenshot, I want something classic, you'll find an example attached, feel free to innovate.

To sum-up :

- One new view for my App
- One new icon
- One marketing screenshot

screen resolution :
640×960
icon resolution :
1024x1024

Target Market(s)

15-30 years

Industry/Entity Type

Marketing

```html
<!DOCTYPE html>
<html lang="en">
<head>
<meta charset="utf-8">
<title>Music Quizz</title>
<link rel="stylesheet" href="https://fonts.googleapis.com/css2?family=Arimo:wght@400;700&display=swap">
<style>
:root{
  --status:#4b4e51;
  --title:#1d3c48;
  --head-a:#6fc7c9;
  --head-b:#a9e0dc;
  --bar:#2a7590;
  --row-a:#3189a6;
  --row-b:#2e839f;
  --row-c:#2c7e99;
  --panel:#286f86;
  --orange:#f28a1c;
  --light:#d7e3e6;
  --teal-light:#9fd0dc;
  --chip:#1f5f74;
  --legend:#d5d9da;
  --card-img:#dde6df;
  --card-txt:#ccd8cc;
  --ink:#111;
}
*{box-sizing:border-box;margin:0;padding:0}
html,body{width:800px;height:1200px;overflow:hidden;background:var(--panel)}
body{font-family:"Arimo",Arial,sans-serif}
.screen{position:absolute;left:0;top:0;width:640px;height:960px;transform:scale(1.25);transform-origin:0 0;background:var(--panel);overflow:hidden}
.abs{position:absolute}
.status-bar{left:0;top:0;width:640px;height:40px;background:var(--status);color:#fff;font-weight:700;font-size:21px}
.status-bar .carrier{left:60px;top:9px;letter-spacing:.5px}
.status-bar .clock{left:0;width:640px;top:9px;text-align:center}
.header{left:0;top:40px;width:640px;height:88px;background:linear-gradient(90deg,var(--head-a),var(--head-b) 50%,var(--head-a));border-bottom:2px solid #1b4a5a}
.header .app-title{left:0;width:640px;top:18px;text-align:center;font-size:45px;font-weight:700;color:var(--title)}
.category-bar{left:0;top:130px;width:640px;height:48px;background:var(--bar);border-bottom:2px solid #24667d}
.category-bar .label{left:12px;top:12px;color:var(--orange);font-weight:700;font-size:21px}
.stripe{left:0;width:640px;height:52px;border-bottom:1px solid #2a7893}
.avatar-ring{left:16px;top:183px;width:150px;height:150px;border-radius:50%;border:7px solid var(--orange);background:radial-gradient(circle at 50% 55%,#3d8ea9,#2a6f88)}
.player-msg{left:182px;top:192px;color:var(--orange);font-weight:700;font-size:25px}
.answer-input{left:182px;top:240px;color:#1e4656;font-size:27px}
.score-line{left:182px;top:295px;color:var(--light);font-weight:700;font-size:21px}
.track-row{left:0;top:338px;width:640px;height:48px;background:var(--row-a)}
.track-row .track{left:26px;top:11px;color:var(--light);font-weight:700;font-size:21px}
.alert-chip{left:186px;top:343px;width:32px;height:32px;background:var(--chip);color:var(--orange);font-weight:700;font-size:28px;text-align:center;line-height:32px}
.history-row{left:0;top:386px;width:640px;height:48px;background:var(--row-b);border-bottom:2px solid #24667d}
.col-head{top:436px;height:46px;background:var(--row-a);color:var(--orange);font-weight:700;font-size:16px;text-align:center;line-height:46px}
.divider{left:319px;top:436px;width:1px;height:524px;background:#3a8aa4}
.legend{left:0;top:482px;width:319px;height:48px;background:var(--legend)}
.ranking{left:18px;top:562px;font-size:21px;line-height:52px;list-style:none}
.ranking .first{color:#fff}.ranking .hot{color:var(--orange)}.ranking .mid{color:var(--teal-light)}.ranking .low{color:var(--light)}
.song-card{left:320px;width:310px;height:94px}
.song-card .art{left:0;top:0;width:107px;height:94px;background:var(--card-img);font-size:26px;color:var(--ink);line-height:94px;text-align:center}
.song-card .meta{left:107px;top:0;width:203px;height:94px;background:var(--card-txt)}
.song-card .song-title{left:12px;top:23px;font-size:26px;font-weight:700;color:var(--ink)}
.song-card .song-artist{left:12px;top:53px;font-size:17px;font-weight:700;color:var(--ink)}
.scroll-track{left:630px;top:482px;width:10px;height:296px;background:#b9c3c4}
.scroll-thumb{left:630px;top:494px;width:10px;height:194px;background:#eef1f1}
</style>
</head>
<body>
<div class="screen">
  <svg width="0" height="0" style="position:absolute">
    <defs>
      <symbol id="ic-mic" viewBox="0 0 32 32"><rect x="12" y="5" width="8" height="14" rx="4" fill="#cfe3ea"/><path d="M9 15a7 7 0 0 0 14 0" fill="none" stroke="#cfe3ea" stroke-width="2"/><rect x="15" y="22" width="2" height="5" fill="#cfe3ea"/><rect x="11" y="26" width="10" height="2" fill="#cfe3ea"/></symbol>
      <symbol id="ic-note" viewBox="0 0 32 32"><path d="M12 7l13-3v16" fill="none" stroke="#f28a1c" stroke-width="3"/><path d="M12 7v17" stroke="#f28a1c" stroke-width="3"/><ellipse cx="9" cy="24" rx="4" ry="3.2" fill="#f28a1c"/><ellipse cx="22" cy="21" rx="4" ry="3.2" fill="#f28a1c"/></symbol>
      <symbol id="ic-quest" viewBox="0 0 32 32"><text x="16" y="27" text-anchor="middle" font-family="Arimo,Arial,sans-serif" font-weight="700" font-size="28" fill="#e8eef0">?</text></symbol>
      <symbol id="ic-star" viewBox="0 0 32 32"><polygon points="16,5 19,13 27.5,13 20.7,18.2 23.2,26.5 16,21.5 8.8,26.5 11.3,18.2 4.5,13 13,13" fill="#fff"/></symbol>
    </defs>
  </svg>

  <div class="abs status-bar">
    <svg class="abs" style="left:6px;top:12px" width="48" height="18"><rect x="0" y="13" width="4" height="5" fill="#fff"/><rect x="7" y="10" width="4" height="8" fill="#fff"/><rect x="14" y="7" width="4" height="11" fill="#fff"/><rect x="21" y="4" width="4" height="14" fill="#fff"/><rect x="28" y="0" width="4" height="18" fill="#fff"/></svg>
    <span class="abs carrier">NEXORA</span>
    <span class="abs clock">2:34</span>
    <svg class="abs" style="left:590px;top:10px" width="42" height="20"><rect x="1" y="1" width="36" height="18" rx="3" fill="none" stroke="#fff" stroke-width="2"/><rect x="4" y="4" width="30" height="12" fill="#fff"/><rect x="38" y="6" width="3" height="8" fill="#fff"/></svg>
  </div>

  <header class="abs header">
    <svg class="abs" style="left:8px;top:14px" width="58" height="60" viewBox="0 0 58 60"><polygon points="29,3 54,16 54,44 29,57 4,44 4,16" fill="none" stroke="#1d3c48" stroke-width="4"/><polygon points="20,30 35,20 35,40" fill="#1d3c48"/></svg>
    <h1 class="abs app-title">Music Quizz</h1>
    <svg class="abs" style="left:573px;top:14px" width="58" height="60" viewBox="0 0 58 60"><polygon points="29,3 54,16 54,44 29,57 4,44 4,16" fill="none" stroke="#1d3c48" stroke-width="4"/><circle cx="29" cy="30" r="8" fill="none" stroke="#1d3c48" stroke-width="5" stroke-dasharray="3 2.2"/><circle cx="29" cy="30" r="5" fill="#1d3c48"/><circle cx="29" cy="30" r="2.2" fill="#8fd4d3"/></svg>
  </header>

  <div class="abs category-bar">
    <span class="abs label">HITS</span>
    <svg class="abs" style="left:586px;top:14px" width="36" height="22"><polygon points="0,0 36,0 18,22" fill="var(--orange)"/></svg>
  </div>

  <div class="abs stripe" style="top:180px;background:var(--row-a)"></div>
  <div class="abs stripe" style="top:232px;background:var(--row-b)"></div>
  <div class="abs stripe" style="top:284px;background:var(--row-c)"></div>

  <div class="abs avatar-ring" role="img" aria-label="Player mascot avatar wearing headphones"></div>
  <p class="abs player-msg">Account was one of the faster !</p>
  <p class="abs answer-input">Type here one artist or title ...</p>
  <p class="abs score-line">YOUR ACCOUNT ( + 18 points )</p>

  <div class="abs track-row"><span class="abs track">Track 12/15</span></div>
  <div class="abs alert-chip">!</div>

  <div class="abs history-row">
    <svg class="abs" style="left:22px;top:8px" width="596" height="32">
      <g fill="#1f5f74">
        <rect x="0" width="32" height="32"/><rect x="40" width="32" height="32"/><rect x="80" width="32" height="32"/><rect x="120" width="32" height="32"/><rect x="160" width="32" height="32"/><rect x="200" width="32" height="32"/><rect x="240" width="32" height="32"/><rect x="280" width="32" height="32"/><rect x="320" width="32" height="32"/><rect x="360" width="32" height="32"/><rect x="400" width="32" height="32"/><rect x="440" width="32" height="32"/>
      </g>
      <g fill="#2a7791"><rect x="480" width="32" height="32"/><rect x="520" width="32" height="32"/><rect x="560" width="32" height="32"/></g>
      <use href="#ic-mic" x="0" width="32" height="32"/>
      <use href="#ic-note" x="40" width="32" height="32"/>
      <use href="#ic-quest" x="80" width="32" height="32"/>
      <use href="#ic-quest" x="120" width="32" height="32"/>
      <use href="#ic-star" x="160" width="32" height="32"/>
      <use href="#ic-mic" x="200" width="32" height="32"/>
      <use href="#ic-mic" x="240" width="32" height="32"/>
      <use href="#ic-note" x="280" width="32" height="32"/>
      <use href="#ic-quest" x="320" width="32" height="32"/>
      <use href="#ic-star" x="360" width="32" height="32"/>
      <use href="#ic-star" x="400" width="32" height="32"/>
      <use href="#ic-star" x="440" width="32" height="32"/>
    </svg>
  </div>

  <div class="abs col-head" style="left:0;width:319px">GLOBAL RANKING</div>
  <div class="abs col-head" style="left:320px;width:320px">YOU HAVE JUST LISTENED TO</div>
  <div class="abs divider"></div>

  <div class="abs legend">
    <svg class="abs" style="left:10px;top:6px" width="300" height="36" font-family="Arimo,Arial,sans-serif" font-size="17">
      <rect x="0" y="2" width="32" height="32" fill="#1f5f74"/><use href="#ic-quest" x="0" y="2" width="32" height="32"/>
      <rect x="32" y="2" width="32" height="32" fill="#fff"/><text x="48" y="24" text-anchor="middle">0</text>
      <rect x="78" y="2" width="32" height="32" fill="#1f5f74"/><use href="#ic-mic" x="78" y="2" width="32" height="32"/>
      <rect x="110" y="2" width="32" height="32" fill="#fff"/><text x="126" y="24" text-anchor="middle">1</text>
      <rect x="156" y="2" width="32" height="32" fill="#1f5f74"/><use href="#ic-note" x="156" y="2" width="32" height="32"/>
      <rect x="188" y="2" width="32" height="32" fill="#fff"/><text x="204" y="24" text-anchor="middle">2</text>
      <rect x="234" y="2" width="32" height="32" fill="#1f5f74"/><use href="#ic-star" x="234" y="2" width="32" height="32"/>
      <rect x="266" y="2" width="32" height="32" fill="#fff"/><text x="282" y="24" text-anchor="middle">1</text>
    </svg>
  </div>

  <ol class="abs ranking">
    <li class="first">1. GAMER 1(29pts)</li>
    <li><span class="low">2. </span><span class="hot">GAMER 2(11pts)</span></li>
    <li><span class="low">3. </span><span class="hot">GAMER 3(14pts)</span></li>
    <li><span class="low">4. </span><span class="mid">GAMER 4(14pts)</span></li>
    <li class="low">5. GAMER 5(-4pts)</li>
  </ol>

  <div class="abs song-card" style="top:483px"><div class="abs art" role="img" aria-label="Album cover">Image</div><div class="abs meta"><span class="abs song-title">Title</span><span class="abs song-artist">Artist</span></div></div>
  <div class="abs song-card" style="top:583px"><div class="abs art" role="img" aria-label="Album cover">Image</div><div class="abs meta"><span class="abs song-title">Title</span><span class="abs song-artist">Artist</span></div></div>
  <div class="abs song-card" style="top:683px"><div class="abs art" role="img" aria-label="Album cover">Image</div><div class="abs meta"><span class="abs song-title">Title</span><span class="abs song-artist">Artist</span></div></div>
  <div class="abs scroll-track"></div>
  <div class="abs scroll-thumb"></div>
</div>
</body>
</html>
```